Payday Lending App Interface Design

Hello, we are building a payday lending application, Lendoro, that lend people money. I have drafted some of the screens that show the functionalities we have at the moment, please find the screens in attachments.
The elements in the screens are placed just to show what should be included in those screens, it's not necessary to follow the same layout. If you have better design ideas, you are very welcomed to show off your talent.
I think what we want is a style guide so that we can apply the same style to any screens that are similar to the ones I attached. We really like
the style as in the attached image called Style.png. We might want something similar - a simple, clean design yet fun and engaging. Customised graphical elements such as icons, illustrations are preferable.
Apart from the attached screens, we might also need a design for the On Board screen and the Login/Sign Up screen too.
Our logo colour is in yellow and black. Perhaps we will have a similar colour theme. I also attached the logo file, icon-Lendoro.png, if you would like to put it in your design.
Please message me if you need further information.
Regards
Target Market(s)
Young people that doesn't have strong income

```html
<!DOCTYPE html>
<html lang="en">
<head>
<meta charset="utf-8">
<title>Lendoro – App Screens</title>
<link href="https://fonts.googleapis.com/css2?family=Lato:wght@400;700;900&display=swap" rel="stylesheet">
<style>
  :root{
    --page:#ececec;
    --screen:#ffffff;
    --ink:#111111;
    --muted:#333333;
    --yellow:#f9d50b;
    --field:#f4f4f4;
    --card-shadow:rgba(0,0,0,.08);
    --tile-red:#fbe1e3;
    --tile-blue:#e6eefc;
    --tile-cream:#fdf3dc;
  }
  *{box-sizing:border-box;margin:0;padding:0}
  html,body{width:1200px;height:789px;overflow:hidden}
  body{background:var(--page);font-family:"Lato",sans-serif;color:var(--ink);position:relative}
  .screen{position:absolute;top:68px;width:302px;height:655px;border-radius:28px;background:var(--screen);overflow:hidden;box-shadow:0 2px 14px rgba(0,0,0,.06)}
  .screen--bank{left:55px}
  .screen--connect{left:449px;background:var(--yellow)}
  .screen--personal{left:843px}
  .status{position:absolute;top:12px;left:0;right:0;height:16px;font-size:10px}
  .status__time{position:absolute;left:30px;top:0}
  .status__icons{position:absolute;right:22px;top:1px}
  .nav-back{position:absolute;left:28px;top:50px}
  .nav-menu{position:absolute;right:26px;top:50px}
  .title{font-weight:700;font-size:20px;letter-spacing:.3px}
  .screen--bank .title{position:absolute;top:87px;width:100%;text-align:center}
  .bank-card{position:absolute;left:26px;width:250px;height:90px;background:#fff;border-radius:4px;box-shadow:0 2px 10px var(--card-shadow)}
  .bank-card__name{position:absolute;left:20px;top:28px;font-weight:700;font-size:13.5px}
  .bank-card__number{position:absolute;left:17px;top:50px;font-size:12.5px;letter-spacing:.2px}
  .bank-card__tile{position:absolute;right:14px;top:17px;width:57px;height:55px;border-radius:6px}
  .tile--red{background:var(--tile-red)}
  .tile--blue{background:var(--tile-blue)}
  .tile--cream{background:var(--tile-cream)}
  .btn{position:absolute;left:26px;width:252px;height:39px;border-radius:6px;background:var(--ink);color:#fff;font-weight:900;display:flex;align-items:center;justify-content:center}
  .screen--bank .btn{top:541px;font-size:13.5px;letter-spacing:.3px}
  .brand{position:absolute;left:0;width:100%;top:355px;text-align:center;font-weight:900;font-size:24px;color:var(--ink)}
  .connect__heading{position:absolute;top:434px;width:100%;text-align:center;font-weight:900;font-size:24px;line-height:29px;letter-spacing:.4px}
  .connect__text{position:absolute;top:500px;width:100%;text-align:center;font-size:12.5px;line-height:29px;color:var(--muted)}
  .screen--personal .title{position:absolute;left:22px;top:104px;font-size:21px}
  .subtitle{position:absolute;left:22px;top:134px;font-size:14px;color:var(--muted)}
  .field{position:absolute;left:22px;width:251px;height:39px;border-radius:6px;background:var(--field);font-size:9px;padding-left:18px;display:flex;align-items:center;color:var(--ink)}
  .screen--personal .btn{left:22px;width:251px;top:384px;font-size:16px;letter-spacing:.3px}
</style>
</head>
<body>

<section class="screen screen--bank">
  <div class="status"><span class="status__time">9:30</span>
    <svg class="status__icons" width="54" height="10" viewBox="0 0 54 10"><rect x="0" y="7" width="2" height="3"/><rect x="3" y="5" width="2" height="5"/><rect x="6" y="3" width="2" height="7"/><rect x="9" y="1" width="2" height="9"/><path d="M16 4a8 8 0 0 1 11 0M18 6a5 5 0 0 1 7 0" fill="none" stroke="#111" stroke-width="1.4"/><circle cx="21.5" cy="8.5" r="1.2"/><rect x="34" y="1.5" width="17" height="7" rx="1.5"/><rect x="51.5" y="3.5" width="1.5" height="3"/></svg>
  </div>
  <svg class="nav-back" width="10" height="14" viewBox="0 0 10 14"><path d="M8 1L2 7l6 6" fill="none" stroke="#111" stroke-width="1.6"/></svg>
  <svg class="nav-menu" width="20" height="16" viewBox="0 0 20 16"><rect y="0" width="20" height="2.4"/><rect y="6.8" width="20" height="2.4"/><rect y="13.6" width="20" height="2.4"/></svg>
  <h1 class="title">Bank Details</h1>

  <div class="bank-card" style="top:137px"><span class="bank-card__name">Halden Bank</span><span class="bank-card__number">1287687965865688</span><span class="bank-card__tile tile--red"></span></div>
  <div class="bank-card" style="top:251px"><span class="bank-card__name">Norvik</span><span class="bank-card__number">97869767568765878</span><span class="bank-card__tile tile--blue"></span></div>
  <div class="bank-card" style="top:365px"><span class="bank-card__name">Meridian Bank</span><span class="bank-card__number">87858658658658765</span><span class="bank-card__tile tile--cream"></span></div>

  <div class="btn">CONNECT BANK ACCOUNT</div>
</section>

<section class="screen screen--connect">
  <div class="status"><span class="status__time">9:30</span>
    <svg class="status__icons" width="54" height="10" viewBox="0 0 54 10"><rect x="0" y="7" width="2" height="3"/><rect x="3" y="5" width="2" height="5"/><rect x="6" y="3" width="2" height="7"/><rect x="9" y="1" width="2" height="9"/><path d="M16 4a8 8 0 0 1 11 0M18 6a5 5 0 0 1 7 0" fill="none" stroke="#111" stroke-width="1.4"/><circle cx="21.5" cy="8.5" r="1.2"/><rect x="34" y="1.5" width="17" height="7" rx="1.5"/><rect x="51.5" y="3.5" width="1.5" height="3"/></svg>
  </div>
  <div class="brand">Lendoro</div>
  <h1 class="connect__heading">Connecting to<br>Your Bank</h1>
  <p class="connect__text">Please don't exit the app. it takes 3-5 minutes<br>to confirm your details with Your bank</p>
</section>

<section class="screen screen--personal">
  <div class="status"><span class="status__time">9:30</span>
    <svg class="status__icons" width="54" height="10" viewBox="0 0 54 10"><rect x="0" y="7" width="2" height="3"/><rect x="3" y="5" width="2" height="5"/><rect x="6" y="3" width="2" height="7"/><rect x="9" y="1" width="2" height="9"/><path d="M16 4a8 8 0 0 1 11 0M18 6a5 5 0 0 1 7 0" fill="none" stroke="#111" stroke-width="1.4"/><circle cx="21.5" cy="8.5" r="1.2"/><rect x="34" y="1.5" width="17" height="7" rx="1.5"/><rect x="51.5" y="3.5" width="1.5" height="3"/></svg>
  </div>
  <svg class="nav-back" width="10" height="14" viewBox="0 0 10 14"><path d="M8 1L2 7l6 6" fill="none" stroke="#111" stroke-width="1.6"/></svg>
  <svg class="nav-menu" width="20" height="16" viewBox="0 0 20 16"><rect y="0" width="20" height="2.4"/><rect y="6.8" width="20" height="2.4"/><rect y="13.6" width="20" height="2.4"/></svg>
  <h1 class="title">Personal Details</h1>
  <p class="subtitle">Please Provide Details as shown on ID</p>
  <div class="field" style="top:173px;padding-left:18px">Given name</div>
  <div class="field" style="top:224px">Middle name</div>
  <div class="field" style="top:276px">Surname</div>
  <div class="field" style="top:328px">Date of Birth ( Day / Month / Year )</div>
  <div class="btn">NEXT</div>
</section>

</body>
</html>
```